Marcus Delbridge Finance

Need a personal website advertising Equipment Finance,Business Finance,Commercial Finance, Construction Finance, Bridging Finance. Similar websites are www.corvalend.com.au / www.tarmivest.com.au / www.qbr7.com.au /wwwhalvecredit.com.au

Target Market(s)

Business People

Industry/Entity Type

Business

Number of Pages Required

3 page

Font styles to use
Serif
Sans Serif

Requirements
Must have
• All i want is a simple corporate looking website advertising Equipment Finance, Commercial Finance, Construction Finance, Business Finance, Bridging Finance,

```html
<!DOCTYPE html>
<html lang="en">
<head>
<meta charset="utf-8">
<title>Marcus Delbridge Finance</title>
<link href="https://fonts.googleapis.com/css2?family=Cinzel:wght@400;600&family=Open+Sans:wght@400;600;700&display=swap" rel="stylesheet">
<style>
:root{
  --blue:#0b6fc0;
  --blue-dark:#075a9e;
  --navy:#10233d;
  --ink:#222;
  --text:#444;
  --muted:#777;
  --grey-band:#ebebeb;
  --light-band:#f2f2f2;
  --white:#fff;
  --footer:#1b1d22;
  --serif:'Cinzel', Georgia, serif;
  --sans:'Open Sans', Arial, sans-serif;
}
*{box-sizing:border-box;margin:0;padding:0}
html,body{width:1200px;height:3186px;overflow:hidden}
body{font-family:var(--sans);color:var(--text);background:var(--white);position:relative}
section,header,nav,footer{position:absolute;left:0;width:1200px}
.heading{font-family:var(--serif);font-weight:400;color:var(--ink);text-align:center;font-size:33px;letter-spacing:1px}
.heading span{color:var(--blue)}

/* Header */
.site-header{top:0;height:102px;background:var(--white)}
.brand{position:absolute;left:40px;top:20px;display:flex;align-items:center;gap:14px}
.brand-square{width:58px;height:58px;background:var(--navy)}
.brand-name{font-family:var(--serif);font-weight:600;color:var(--navy);font-size:23px;line-height:28px;letter-spacing:.5px}
.call{position:absolute;right:40px;top:28px;display:flex;gap:10px;align-items:center}
.call-label{font-family:var(--serif);color:var(--blue);font-size:13px;letter-spacing:.5px}
.call-number{font-size:24px;color:var(--ink);line-height:26px}

/* Nav */
.main-nav{top:102px;height:51px;background:var(--blue);display:flex;align-items:center;justify-content:space-between;padding:0 38px 0 38px}
.main-nav a{color:var(--white);text-decoration:none;font-size:17px;letter-spacing:.3px;line-height:51px;padding:0 20px}
.main-nav a.active{background:#111}

/* Hero */
.hero{top:153px;height:446px;background:linear-gradient(110deg,#c9d8ea 0%,#8fa9c8 35%,#b8cbe0 60%,#5f7fa5 100%)}
.hero-badge{position:absolute;left:810px;top:78px;width:300px;height:300px;border-radius:50%;background:var(--white);border:14px solid #1a1d24;display:flex;flex-direction:column;align-items:center;justify-content:center;text-align:center}
.hero-badge h2{font-family:var(--serif);font-weight:400;color:var(--blue);font-size:22px;line-height:28px;margin-bottom:18px}
.btn-blue{background:var(--blue);color:var(--white);font-weight:700;font-size:14px;padding:10px 16px}

/* About */
.about{top:599px;height:310px}
.about .heading{margin-top:34px}
.about p{width:1120px;margin:22px auto 0;text-align:center;font-size:13.4px;line-height:24px}
.btn-grey{display:block;width:108px;margin:28px auto 0;background:#e2e2e2;color:var(--ink);font-size:13px;text-align:center;line-height:40px;box-shadow:0 1px 2px rgba(0,0,0,.2)}

/* Services */
.services{top:909px;height:493px;background:var(--grey-band)}
.services .heading{margin-top:40px}
.service{position:absolute;overflow:hidden}
.service-label{position:absolute;left:0;right:0;bottom:0;height:46px;background:rgba(20,20,20,.75);color:var(--white);font-weight:700;font-size:18px;text-align:center;line-height:46px}

/* News */
.news{top:1402px;height:478px}
.news .heading{margin-top:40px}
.news-card{position:absolute;top:110px;height:268px}
.news-photo{position:absolute;left:0;top:0;width:240px;height:268px}
.news-date{position:absolute;left:188px;top:102px;width:52px;background:var(--white);text-align:center}
.news-date b{display:block;font-weight:400;font-size:26px;color:#333;line-height:38px}
.news-date i{display:block;font-style:normal;background:var(--blue);color:var(--white);font-size:17px;line-height:32px}
.news-body{position:absolute;left:240px;top:0;width:266px;height:268px;background:var(--white);box-shadow:2px 3px 6px rgba(0,0,0,.25);clip-path:polygon(0 0,100% 0,95% 100%,0 100%);padding:48px 28px 0 16px}
.news-body h3{color:var(--blue);font-size:16px;font-weight:600;line-height:20px}
.news-body p{margin-top:12px;font-size:13px;line-height:19px;text-align:justify}
.news-body a{display:block;margin-top:8px;color:var(--blue);font-size:13px;text-decoration:none}
.dots{position:absolute;top:438px;left:528px;display:flex;gap:4px}
.dots span{width:40px;height:5px;background:#eee}
.dots span.on{background:var(--blue)}

/* Why */
.why{top:1880px;height:361px;background:var(--grey-band)}
.why .heading{margin-top:44px}
.why .intro{width:930px;margin:20px auto 0;text-align:center;font-size:13.4px;line-height:24px}
.feature{position:absolute;top:206px;width:240px;text-align:center}
.feature svg{display:block;margin:0 auto}
.feature h4{font-family:var(--serif);color:var(--blue-dark);font-weight:600;font-size:16px;margin-top:14px}
.feature p{font-size:10.5px;color:var(--muted);line-height:15px;margin-top:8px}

/* Testimonials */
.testimonials{top:2241px;height:431px}
.testimonials .heading{margin-top:34px}
.quote-text{position:absolute;left:234px;top:102px;width:760px;text-align:center;font-size:13.4px;line-height:24px}
.quote-mark{position:absolute;font-family:Georgia,serif;color:var(--blue);font-size:88px;line-height:1}
.divider{position:absolute;left:234px;top:212px;width:722px;height:1px;background:#ccc}
.divider::after{content:"";position:absolute;left:355px;top:-1px;border:6px solid transparent;border-top-color:#bbb}
.avatar{position:absolute;border-radius:50%;background:linear-gradient(160deg,#c9b39b,#6d5a4a)}
.reviewer{position:absolute;top:344px;width:1200px;text-align:center;font-family:var(--serif);color:var(--blue);font-size:18px;letter-spacing:1px}
.stars{position:absolute;top:374px;width:1200px;display:flex;justify-content:center;gap:4px}

/* Clients */
.clients{top:2672px;height:125px;background:var(--light-band)}
.clients-title{position:absolute;left:92px;top:30px;font-family:var(--serif);font-size:28px;line-height:30px;color:var(--ink);text-align:center}
.client{position:absolute;top:36px;width:146px;height:68px;background:var(--white);box-shadow:0 1px 3px rgba(0,0,0,.15);display:flex;align-items:center;justify-content:center;font-weight:700;font-size:17px;color:var(--navy)}

/* Footer */
.site-footer{top:2797px;height:336px;background:linear-gradient(180deg,#15171b 0%,#26292f 70%,#3a3e45 100%);color:#cfd2d6}
.footer-title{position:absolute;top:44px;font-family:var(--serif);font-size:18px;color:var(--white);letter-spacing:1px}
.footer-rule{position:absolute;top:76px;height:1px;background:#3d4047}
.quick-links{position:absolute;left:83px;top:90px;list-style:none}
.quick-links li{font-size:12px;line-height:33px;color:#cfd2d6}
.quick-links li::before{content:"›";margin-right:6px;color:#888}
.quick-links li.active{color:var(--blue)}
.contact-item{position:absolute;left:329px;display:flex;gap:12px;font-size:12.5px;line-height:18px}
.map{position:absolute;left:641px;top:106px;width:262px;height:177px;background:linear-gradient(135deg,#e8e6df,#d6e3cf)}
.footer-brand{position:absolute;left:966px;top:186px;width:200px;text-align:center;font-family:var(--serif);color:var(--white);font-size:24px;line-height:32px}
.bottom-bar{top:3133px;height:53px;background:var(--blue);color:var(--white)}
.bottom-bar p{position:absolute;left:83px;top:18px;font-size:13px}
.socials{position:absolute;left:988px;top:9px;display:flex;gap:6px}
.socials span{width:36px;height:36px;border-radius:50%;border:2px solid var(--white);background:var(--blue-dark)}
</style>
</head>
<body>

<header class="site-header">
  <div class="brand">
    <div class="brand-square"></div>
    <div class="brand-name">MARCUS DELBRIDGE<br>FINANCE</div>
  </div>
  <div class="call">
    <svg width="42" height="42" viewBox="0 0 42 42"><circle cx="21" cy="21" r="19" fill="none" stroke="#0b6fc0" stroke-width="2.5"/><path d="M14 12c2-1 3 0 4 3s-1 3-1 4 3 5 5 5 2-2 4-1 3 2 2 4-3 3-6 2-10-7-10-12 0-4 2-5z" fill="#0b6fc0"/></svg>
    <div><div class="call-label">CALL US TODAY</div><div class="call-number">555-218-4470</div></div>
  </div>
</header>

<nav class="main-nav">
  <a class="active">HOME</a><a>ABOUT US</a><a>OUR SERVICS</a><a>RESOURCES</a><a>LATEST NEWS</a><a>CONTACT US</a>
</nav>

<section class="hero" role="img" aria-label="Businessman's hand touching a glowing financial chart on a blue screen">
  <div class="hero-badge">
    <h2>SOLUTIONS THAT<br>NEVER MISS THE AIM</h2>
    <span class="btn-blue">Get A Free Consultation</span>
  </div>
</section>

<section class="about">
  <h2 class="heading">ABOUT MARCUS DELBRIDGE <span>- FINANCE</span></h2>
  <p>Lorem ipsum dolor sit amet, consectetuer adipiscing elit, sed diam nonummy nibh euismod tincidunt ut laoreet dolore magna aliquam erat volutpat. Ut wisi enim ad minim veniam, quis nostrud exerci tation ullamcorper suscipit lobortis nisl ut aliquip ex ea commodo consequat. Duis autem vel eum iriure dolor in hendrerit in vulputate velit esse molestie consequat, vel illum dolore eu feugiat nulla facilisis at vero eros et accumsan et iusto odio dignissim qui blandit praesent luptatum zzril delenit augue duis dolore te feugait nulla facilisi.</p>
  <span class="btn-grey">Read More</span>
</section>

<section class="services">
  <h2 class="heading">OUR <span>SERVICES</span></h2>
  <div class="service" style="left:38px;top:117px;width:285px;height:329px;background:linear-gradient(180deg,#8fc1e8,#c79a3a 70%,#6b6458)" role="img" aria-label="Excavator on a construction site"><div class="service-label">Equipment Finance</div></div>
  <div class="service" style="left:333px;top:117px;width:262px;height:157px;background:linear-gradient(135deg,#e9eef2,#8fb6c9)" role="img" aria-label="Hands working with a calculator and documents"><div class="service-label">Business Finance</div></div>
  <div class="service" style="left:607px;top:117px;width:258px;height:157px;background:linear-gradient(135deg,#e9eef2,#8fb6c9)" role="img" aria-label="Hands working with a calculator and documents"><div class="service-label">Commercial Finance</div></div>
  <div class="service" style="left:333px;top:287px;width:532px;height:159px;background:linear-gradient(90deg,#6e6e6e,#e5c21e 45%,#c99a2b 80%,#eee)" role="img" aria-label="Toy loader beside stacks of gold coins"><div class="service-label">Construction Finance</div></div>
  <div class="service" style="left:879px;top:117px;width:283px;height:329px;background:linear-gradient(180deg,#bcd3ea,#e9f0f6 55%,#5e6b78)" role="img" aria-label="Businessman leaping across a gap in a broken bridge"><div class="service-label">Bridging Finance</div></div>
</section>

<section class="news">
  <h2 class="heading">LATEST <span>NEWS</span></h2>
  <article class="news-card" style="left:89px">
    <div class="news-photo" style="background:linear-gradient(135deg,#dfe6ec,#a7b6c4)" role="img" aria-label="Business people fitting coloured puzzle pieces together"></div>
    <div class="news-date"><b>17</b><i>Jan</i></div>
    <div class="news-body">
      <h3>Coastal Trade Forum marks 10 years in operation</h3>
      <p>Duis autl vel eum iriure dolor in lk hendr vulputatel velit es molestie conl quat, vel illum dol dignissim qui blandit praesen lup delenitnil lanre facilisi.</p>
      <a>Read More »</a>
    </div>
  </article>
  <article class="news-card" style="left:622px">
    <div class="news-photo" style="background:linear-gradient(180deg,#8aa0b5,#3a4250 60%,#9a9a9a)" role="img" aria-label="Group of officials standing together outdoors"></div>
    <div class="news-date"><b>17</b><i>Jan</i></div>
    <div class="news-body">
      <h3>Regional council vows to extend lending reforms</h3>
      <p>Duis autl vel eum iriure dolor in lk hendr vulputatel velit es molestie conl quat, vel illum dol dignissim qui blandit praesen lup delenitnil lanre facilisi.</p>
      <a>Read More »</a>
    </div>
  </article>
  <div class="dots"><span></span><span class="on"></span><span></span></div>
</section>

<section class="why">
  <h2 class="heading">WHY <span>CHOOSE US?</span></h2>
  <p class="intro">Duis autem vel eum iriure dolor in hendrerit in vulputate velit esse molestie consequat, vel illum dolore eu feugiat nulla facilisis at vero eros et accumsan et iusto odio dignissim qui blandit delenit augue duis dolore te feugait nulla facilisi.</p>
  <div class="feature" style="left:71px">
    <svg width="70" height="56" viewBox="0 0 70 56"><circle cx="42" cy="14" r="12" fill="#0b6fc0"/><text x="42" y="20" font-size="16" font-family="Arial" font-weight="700" fill="#fff" text-anchor="middle">$</text><path d="M4 40h14l12 4h16c3 0 3 4 0 4H30M18 52l16 2 30-14c3-2 0-6-3-4L46 44" fill="none" stroke="#10233d" stroke-width="4" stroke-linecap="round"/></svg>
    <h4>COST EFFECTIVE</h4><p>Sed ut perspiciatis unde omnis<br>iste natus error sdolorernque.</p>
  </div>
  <div class="feature" style="left:337px">
    <svg width="56" height="60" viewBox="0 0 56 60"><circle cx="28" cy="22" r="18" fill="none" stroke="#10233d" stroke-width="5"/><circle cx="28" cy="22" r="9" fill="#0b6fc0"/><path d="M16 36l-6 20 8-4 5 7 5-16M40 36l6 20-8-4-5 7-5-16" fill="#10233d"/></svg>
    <h4>YEARS OF EXPERIENCE</h4><p>Sed ut perspiciatis unde omnis<br>iste natus error sdolorernque.</p>
  </div>
  <div class="feature" style="left:623px">
    <svg width="70" height="60" viewBox="0 0 70 60"><circle cx="42" cy="34" r="22" fill="none" stroke="#10233d" stroke-width="5"/><path d="M42 34V20M42 34l9 6" stroke="#0b6fc0" stroke-width="4" stroke-linecap="round"/><rect x="37" y="4" width="10" height="6" fill="#10233d"/><path d="M2 26h14M6 34h10M2 42h14" stroke="#0b6fc0" stroke-width="4" stroke-linecap="round"/></svg>
    <h4>SPEEDY SOLUTION</h4><p>Sed ut perspiciatis unde omnis<br>iste natus error sdolorernque.</p>
  </div>
  <div class="feature" style="left:889px">
    <svg width="60" height="60" viewBox="0 0 60 60"><path d="M30 2l7 6 9-1 3 9 8 5-3 9 3 9-8 5-3 9-9-1-7 6-7-6-9 1-3-9-8-5 3-9-3-9 8-5 3-9 9 1z" fill="#10233d"/><path d="M19 31l8 8 15-16" fill="none" stroke="#fff" stroke-width="5" stroke-linecap="round" stroke-linejoin="round"/></svg>
    <h4>100% GAURANTEED</h4><p>Sed ut perspiciatis unde omnis<br>iste natus error sdolorernque.</p>
  </div>
</section>

<section class="testimonials">
  <h2 class="heading">CLIENT <span>TESTIMONIALS</span></h2>
  <span class="quote-mark" style="left:160px;top:100px">“</span>
  <p class="quote-text">Lorem ipsum dolor sit amet, consectetuer adipiscing elit, sed diam nonummy nibh euismod tincidunt ut laoreet dolore magna aliquam erat volutpat. Ut wisi enim ad minim veniam, quis nostrud exer tation ullamcorper suscipit lobout laoreet consequat. Duis autem vel dolor i et ace te aliquam erat volutpat facilisi.</p>
  <span class="quote-mark" style="left:986px;top:148px">”</span>
  <div class="divider"></div>
  <div class="avatar" style="left:465px;top:250px;width:72px;height:72px" role="img" aria-label="Client portrait"></div>
  <div class="avatar" style="left:557px;top:245px;width:84px;height:84px;border:4px solid #0b6fc0" role="img" aria-label="Client portrait"></div>
  <div class="avatar" style="left:661px;top:250px;width:72px;height:72px" role="img" aria-label="Client portrait"></div>
  <div class="reviewer">DANIEL HARROW</div>
  <div class="stars">
    <svg width="96" height="18" viewBox="0 0 96 18"><g fill="#0b6fc0"><path id="s" d="M9 1l2.4 5.2 5.6.6-4.2 3.8 1.2 5.6L9 13.4 4 16.2l1.2-5.6L1 6.8l5.6-.6z"/><use href="#s" x="19"/><use href="#s" x="38"/><use href="#s" x="57"/></g><use href="#s" x="76" fill="#999"/></svg>
  </div>
</section>

<section class="clients">
  <div class="clients-title">OUR<br>CLIENTS</div>
  <svg style="position:absolute;left:170px;top:28px" width="28" height="72" viewBox="0 0 28 72"><path d="M4 2l20 34L4 70" fill="none" stroke="#bbb" stroke-width="3"/></svg>
  <div class="client" style="left:221px">Brightwire</div>
  <div class="client" style="left:399px">Kelvara</div>
  <div class="client" style="left:576px">Ostrel</div>
  <div class="client" style="left:754px">Pyrnex</div>
  <div class="client" style="left:932px">Veldan Power</div>
  <svg style="position:absolute;left:1105px;top:40px" width="60" height="60" viewBox="0 0 60 60"><circle cx="30" cy="30" r="27" fill="none" stroke="#ddd" stroke-width="2"/><path d="M25 18l12 12-12 12" fill="none" stroke="#ddd" stroke-width="3"/></svg>
</section>

<footer class="site-footer">
  <h3 class="footer-title" style="left:83px">QUICK LINKS</h3>
  <div class="footer-rule" style="left:83px;width:180px"></div>
  <ul class="quick-links">
    <li class="active">Home</li><li>About Us</li><li>Our Services</li><li>Resources</li><li>Latest News</li><li>Contact Us</li>
  </ul>

  <h3 class="footer-title" style="left:329px">CONTACT DETAIL</h3>
  <div class="footer-rule" style="left:329px;width:250px"></div>
  <div class="contact-item" style="top:102px">
    <svg width="14" height="20" viewBox="0 0 14 20"><path d="M7 0a7 7 0 0 1 7 7c0 5-7 13-7 13S0 12 0 7a7 7 0 0 1 7-7z" fill="#0b6fc0"/><circle cx="7" cy="7" r="2.5" fill="#1b1d22"/></svg>
    <div>Marcus Delbridge Finance<br>418 Harbour Lane, Suite 12<br>Marlow Bay, HI 96820</div>
  </div>
  <div class="contact-item" style="top:200px">
    <svg width="16" height="16" viewBox="0 0 16 16"><path d="M3 1c1.5-.5 2 .5 2.5 2S5 5 5 5.5 7 9.5 9.5 10.5c.8 0 1-1.5 2.5-1s2 1 1.5 2.5-2 2.5-4 2S1 8 1.5 4 2 1.5 3 1z" fill="#0b6fc0"/></svg>
    <div>555-218-4470</div>
  </div>
  <div class="contact-item" style="top:265px">
    <svg width="16" height="12" viewBox="0 0 16 12"><rect width="16" height="12" fill="#0b6fc0"/><path d="M0 0l8 6 8-6" fill="none" stroke="#1b1d22" stroke-width="1.5"/></svg>
    <div>info@delbridgefinance.com</div>
  </div>

  <h3 class="footer-title" style="left:641px">LOCATION MAP</h3>
  <div class="map" role="img" aria-label="Street map showing the office location"></div>

  <div class="footer-brand">MARCUS<br>DELBRIDGE<br>FINANCE</div>
</footer>

<footer class="bottom-bar">
  <p>Copyright © 2016 Marcus Delbridge Finance . All Rights Reserved.</p>
  <div class="socials"><span></span><span></span><span></span><span></span></div>
</footer>

</body>
</html>
```